Home page design for Drone video business (the Business focusses on home videos for realtors)

Dear reader,

*I NEED DESIGNS OF ALL THE PAGES*
We need a first design of a homepage and of 4 other pages of the website of a business that sells drone video services. All the pages will need to be in the similar design style.
The video's are targeted at consumers that want to sell there home and would like to have a cool drone video of photos of their home.

How does the website look:
- has a navbar on top
- A cool looking banner of an areal drone.
- A Big header: with company name: SkyLoftReels
- A smaller subheader: We film your home to increase your chances of sale
- Then a section with a Big header: How does it work
- In this section a place for a vimeo explainitory video
- Then a similar navbar styled bar with a phone number and a email address
- Then a section where the videos porfolio is displayed in a cool way
- Inside this sectiona header: Our work

- A section with header: Why us?
- 4 symbols here with a subheader and some lorum ipsum text underneath (see wireframe images)

- Under that a: Contact us
- where you can put in name, email, phone, message box and a send button

- At the bottom a footer with phone number and a fake address for now.

Be creative. Use creative but serious color.
Use a serious font. Make it a sharp design. Sharp lines. Not to dark design and not to light design.

The wireframes are the same kind of images.
PLEASE PUT IN DESIGNS OF ALL THE PAGES

Good luck

Target Market(s)

People that want to sell home and want to make a cool drone video or photos of their home.

Industry/Entity Type

Business

Contact Information for Business Card

Lucas Wenning
lucas@skyloftreels.example
+31647208351

Logo Text

SkyLoftReels

Number of Pages Required

1 page

Font styles to use
Sans Serif

Requirements
Must have
• All the sections as explained in the instructions.
• The nav bar should have an about us, services, portfolio and a contact us buttons.
• See instruction for details.
• Must include designs of the front page, contact us, our services, portfolio and contact us.
• If you do add some designs for the "about us", "services", "prices", "portfolio" and "contact us" pages, you make a way better chance of winning the competition.
Nice to have
• designs for the other pages as described at the Must haves. You make a better chance of winning if you include them. Look at the wireframes to see the mockups for those pages. think creative about what kind of sections and design should be included in those pages.
Should not have
• bad designs.

```html
<!DOCTYPE html>
<html lang="en">
<head>
<meta charset="utf-8">
<title>SkyLoftReels – Our Services</title>
<link rel="stylesheet" href="https://fonts.googleapis.com/css2?family=Open+Sans:wght@400;600;700&display=swap">
<style>
:root{
  --slate:#4a5259;
  --slate-dark:#353c42;
  --hero:#3a3f44;
  --green:#7ab51d;
  --green-dark:#6a9c1a;
  --blue:#0f9bd7;
  --white:#ffffff;
  --ink:#2f3438;
}
*{margin:0;padding:0;box-sizing:border-box}
html,body{width:814px;height:1200px;overflow:hidden}
body{position:relative;background:var(--slate);font-family:"Open Sans",Arial,sans-serif;color:var(--white)}
.abs{position:absolute}

/* header */
.site-header{left:0;top:0;width:814px;height:51px;background:var(--slate);border-bottom:3px solid var(--green);z-index:3}
.brand{left:112px;top:0;width:106px;height:61px;background:var(--white);border-radius:0 0 8px 8px;display:flex;align-items:center;justify-content:center;z-index:4;box-shadow:0 2px 4px rgba(0,0,0,.3)}
.brand span{color:var(--green);font-weight:700;font-size:13px}
.nav{left:0;top:0;z-index:4}
.nav a{position:absolute;top:17px;font-size:12px;font-weight:600;letter-spacing:.6px;color:var(--white);text-decoration:none;white-space:nowrap}
.nav a.active{top:10px;left:370px;width:88px;height:27px;line-height:27px;text-align:center;background:var(--white);color:var(--green);border-radius:14px}

/* hero */
.hero{left:0;top:0;width:814px;height:232px;background:linear-gradient(120deg,#2c3034 0%,#4a4e52 45%,#34383c 100%)}
.hero-title{left:0;top:82px;width:814px;text-align:center;font-size:27px;font-weight:600;letter-spacing:1px}
.hero-rule{left:363px;top:125px;width:80px;height:3px;background:var(--green)}
.hero-sub{left:0;top:141px;width:814px;text-align:center;font-size:10.5px;font-weight:600;line-height:13px}

/* tabs */
.tab{top:259px;height:28px;line-height:28px;font-size:12px;font-weight:600;padding:0 17px}
.tab.active{background:var(--blue)}

/* service items */
.media{width:208px;height:136px;background:linear-gradient(160deg,#9fc3df 0%,#b9a58a 55%,#5a5048 100%)}
.media.m2{background:linear-gradient(170deg,#cfd6dc 0%,#8e8a84 55%,#3d3a36 100%)}
.media.m3{background:linear-gradient(170deg,#dfe3e6 0%,#a9b0b4 50%,#c6552a 100%)}
.play{position:absolute;left:88px;top:55px;width:41px;height:26px;background:var(--blue)}
.play svg{display:block;margin:6px auto 0}
.svc-title{left:369px;font-size:18px;font-weight:600;color:var(--green);letter-spacing:.4px}
.svc-text{left:369px;font-size:11px;font-weight:600;line-height:14.5px;letter-spacing:.2px}
.starts{left:370px;font-size:18px;letter-spacing:.3px}
.price{left:463px;width:89px;height:34px;line-height:34px;text-align:center;background:var(--blue);font-size:17px;font-weight:600}
.btn-more{left:338px;top:844px;width:123px;height:31px;line-height:31px;text-align:center;background:var(--blue);font-size:13px;font-weight:600}

/* request band */
.request{left:0;top:898px;width:814px;height:68px;background:var(--green)}
.request-title{left:94px;top:913px;font-size:24px;font-weight:700;letter-spacing:.6px;text-shadow:1px 1px 2px rgba(0,0,0,.35)}
.request-btn{left:528px;top:910px;width:202px;height:44px;line-height:42px;text-align:center;background:var(--green-dark);border-left:2px solid #4d7412;border-bottom:2px solid #4d7412;font-size:20px;font-weight:600;letter-spacing:1px;text-shadow:1px 1px 2px rgba(0,0,0,.35)}

/* footer */
.footer{left:0;top:966px;width:814px;height:194px;background:var(--slate-dark)}
.f-head{font-size:15px;font-weight:600;letter-spacing:.6px}
.f-rule{height:3px;width:78px;background:var(--green)}
.f-about{left:94px;top:1039px;font-size:12px;font-weight:600;line-height:20.7px;letter-spacing:.3px}
.f-links{left:329px;top:1042px;list-style:none}
.f-links li{font-size:10px;font-weight:700;letter-spacing:.8px;height:20.5px}
.f-links li b{color:var(--green);display:inline-block;width:22px}
.f-input{left:538px;top:1045px;width:172px;height:30px;background:var(--white);border:1px solid #ccc;color:#888;font-size:10px;line-height:28px;padding-left:15px;font-family:Arial,sans-serif}
.f-subscribe{left:538px;top:1090px;width:108px;height:28px;line-height:28px;text-align:center;background:var(--green);font-size:13px;font-weight:700;letter-spacing:1px}
.to-top{left:774px;top:1136px;width:34px;height:32px;background:var(--green)}
.to-top svg{display:block;margin:12px auto 0}

.bottom-bar{left:0;top:1160px;width:814px;height:40px;background:var(--slate)}
.copyright{left:94px;top:1168px;font-size:13.5px;font-weight:600;letter-spacing:.3px}
.social{top:1166px;width:29px;height:29px;background:var(--slate-dark)}
</style>
</head>
<body>

<section class="abs hero" role="img" aria-label="Dark photo of a hand writing with a pen on paper"></section>
<div class="abs site-header"></div>
<div class="abs brand"><span>SkyLoftReels</span></div>
<nav class="abs nav">
  <a style="left:324px">HOME</a>
  <a class="active">SERVICES</a>
  <a style="left:468px">ABOUT US</a>
  <a style="left:554px">PORTFOLIO</a>
  <a style="left:644px">CONTACT</a>
</nav>

<h1 class="abs hero-title">OUR SERVICES</h1>
<div class="abs hero-rule"></div>
<p class="abs hero-sub">Lorem ipsum dolor sit amet consectetuer<br>adipiscing elit. Suspendisse et justo.</p>

<div class="abs tab active" style="left:125px">Category 1</div>
<div class="abs tab" style="left:214px">Category 2</div>
<div class="abs tab" style="left:303px">Category 3</div>
<div class="abs tab" style="left:391px">Category 3</div>
<div class="abs tab" style="left:480px">Category 4</div>

<!-- service 1 -->
<div class="abs media" style="left:126px;top:320px" role="img" aria-label="Video still of a surveyor in a hard hat flying a drone">
  <div class="play"><svg width="12" height="14" viewBox="0 0 12 14"><path d="M0 0 L12 7 L0 14Z" fill="#fff"/></svg></div>
</div>
<h2 class="abs svc-title" style="top:317px">4K VIDEOS</h2>
<p class="abs svc-text" style="top:353px">Lorem ipsum dolor sit amet consectetuer adipiscing elit.<br>Lorem ipsum dolor sit amet consectetuer adipiscing elit.<br>Lorem ipsum dolor sit amet consectetuer adipiscing elit.</p>
<div class="abs starts" style="top:413px">Starts at</div>
<div class="abs price" style="top:410px">499 $</div>

<!-- service 2 -->
<div class="abs media m2" style="left:126px;top:492px" role="img" aria-label="Video still of a worker preparing a drone on a parking lot">
  <div class="play"><svg width="12" height="14" viewBox="0 0 12 14"><path d="M0 0 L12 7 L0 14Z" fill="#fff"/></svg></div>
</div>
<h2 class="abs svc-title" style="top:488px">HD CLERIALPHOTOS</h2>
<p class="abs svc-text" style="top:526px">Lorem ipsum dolor sit amet consectetuer adipiscing elit.<br>Lorem ipsum dolor sit amet consectetuer adipiscing elit.<br>Lorem ipsum dolor sit amet consectetuer adipiscing elit.</p>
<div class="abs starts" style="top:586px">Starts at</div>
<div class="abs price" style="top:582px">199 $</div>

<!-- service 3 -->
<div class="abs media m3" style="left:124px;top:668px;width:211px;height:140px" role="img" aria-label="Video still of an engineer near wind turbines with a drone">
  <div class="play" style="left:90px;top:62px"><svg width="12" height="14" viewBox="0 0 12 14"><path d="M0 0 L12 7 L0 14Z" fill="#fff"/></svg></div>
</div>
<h2 class="abs svc-title" style="top:665px">NEIGHBOURHOOD VIDEOS</h2>
<p class="abs svc-text" style="top:703px">Lorem ipsum dolor sit amet consectetuer adipiscing elit.<br>Lorem ipsum dolor sit amet consectetuer adipiscing elit.<br>Lorem ipsum dolor sit amet consectetuer adipiscing elit.</p>
<div class="abs starts" style="top:763px">Starts at</div>
<div class="abs price" style="top:759px">399 $</div>

<div class="abs btn-more">LOAD MORE</div>

<section class="abs request"></section>
<h2 class="abs request-title">GOT A SPECIAL REQUEST ?</h2>
<div class="abs request-btn">CONTACT US</div>

<footer class="abs footer"></footer>
<h3 class="abs f-head" style="left:94px;top:990px">ABOUT US</h3>
<div class="abs f-rule" style="left:94px;top:1021px"></div>
<p class="abs f-about">Lorem ipsum dolor sit<br>consectetuer adipiscing.<br>Suspendisse et justo.<br>Suspendisse et justo.</p>

<h3 class="abs f-head" style="left:329px;top:992px">USEFULL LINKS</h3>
<div class="abs f-rule" style="left:329px;top:1023px"></div>
<ul class="abs f-links">
  <li><b>&gt;</b>HOME</li>
  <li><b>&gt;</b>PORTFOLIO</li>
  <li><b>&gt;</b>CONTACT US</li>
  <li><b>&gt;</b>SERVICES</li>
</ul>

<h3 class="abs f-head" style="left:537px;top:995px">NEWSLETTER</h3>
<div class="abs f-rule" style="left:537px;top:1025px"></div>
<div class="abs f-input">Your email Address...</div>
<div class="abs f-subscribe">SUBCRIBE</div>

<div class="abs to-top"><svg width="8" height="5" viewBox="0 0 8 5"><path d="M0 5 L4 0 L8 5Z" fill="#fff"/></svg></div>

<div class="abs bottom-bar"></div>
<p class="abs copyright">© SkyLoftReels 2016.</p>
<div class="abs social" style="left:570px"></div>
<div class="abs social" style="left:601px"></div>
<div class="abs social" style="left:632px"></div>
<div class="abs social" style="left:663px"></div>
<div class="abs social" style="left:694px"></div>

</body>
</html>
```